Dashboard Elements

Hello – looking for someone to create dashboard elements.
I’ve already basically designed all these elements – but I need someone to take what I’ve designed and make it look like an actual dashboard UI, like an app - assuming using some kind of dashboard UI kit (but however you would like to get it done is fine). It can look just like mine or try something different, as long as it matches the color scheme webpage that I’m going to out it on – see the page here. I’m ok with making it dark, maybe that would look better – again as long as it matches the webpage (https://www.plandeck.io/file/7QxKtr2BwLpZnVe4Hs8Mc1/Webpage-with-placeholders?node-id=0%3A1). Please note, you do not need to put anything on the webpage or do anything with this Figma file, this is just a reference so you can color/stylize it accordingly.

The attached Powerpoint file has everything you need - make sure to zoom all the way out to see everything on the slides.

Here are the Dashboard elements needed (this will all make sense when you look at the PPT):
Dashboard 1
Dashboard 1 – expanded view A
Dashboard 1 – expanded view B
View Source button by itself
Source Document Viewer 1 and 2 (these are exactly the same just with a different image inside)*
Dashboard 2 (only slightly different than Dashboard 1, just extended with extra headings
Table of Contents
Searchbar and Source Doc by itself
*the documents in the source document viewers should still look like documents - they don’t need to look like part of the UI, because this is a document viewer – you can restyle/recolor if necessary or just leave these as is.
- Colors must match color scheme of webpage, attached and on Figma link (images there currently are only placeholders) – ok to go dark as long as it matches
- Must look sleek, clean, realistic
- Don’t add any pictures of people or change the text.
- In case it’s not clear, this is what I mean by the concept of Dashboard UI - https://www.notavia.net/shard/s7/sh/8fad21bc-14e9-4a7c-b2d0-5c3e9f71a604/92c4e1b7a05d3f68e1c2b947d0a3f815
- Must be sent in an editable file, I may need to be edit text and other elements
- If you are going to send a sample, please make sure it’s part of the dashboard itself, not just the table of contents etc

Ideally hoping to find someone I can continue working with as I'll have a lot more graphic design work needed coming up.

Thank you!

```html
<!DOCTYPE html>
<html lang="en">
<head>
<meta charset="utf-8">
<title>Dashboard Elements – C-CDA Compendium</title>
<link rel="stylesheet" href="https://fonts.googleapis.com/css2?family=Ubuntu:wght@400;500&family=Lato:wght@400;700&display=swap">
<style>
:root{
  --bg:#100d1f;
  --bg-glow:#4b3a8c;
  --panel:#1c1830;
  --card:#1a1630;
  --band:#221d3b;
  --band-dark:#17132a;
  --teal:#16b3a6;
  --teal-soft:#1fc9b9;
  --purple:#7d6be3;
  --purple-soft:#9686f0;
  --text:#ffffff;
  --muted:#c9c4e6;
  --heading:#7f6fe6;
}
*{box-sizing:border-box;margin:0;padding:0}
html,body{width:1200px;height:842px;overflow:hidden}
body{
  position:relative;
  background:
    radial-gradient(ellipse 520px 420px at 80px 560px, #4a3a8f 0%, rgba(74,58,143,0) 70%),
    radial-gradient(ellipse 520px 300px at 1150px 842px, #153b4a 0%, rgba(21,59,74,0) 70%),
    var(--bg);
  font-family:"Lato",sans-serif;
  color:var(--text);
}
.board-title{
  position:absolute;
  font-family:"Ubuntu",sans-serif;
  font-weight:500;
  font-size:32px;
  color:var(--heading);
  letter-spacing:.3px;
}
.board-title--d1{left:133px;top:38px}
.board-title--a{left:770px;top:38px}
.board-title--b{left:747px;top:789px}

.panel{position:absolute;background:var(--panel);overflow:hidden}
.panel--d1{left:20px;top:108px;width:561px;height:339px}
.panel--a{left:599px;top:108px;width:561px;height:339px}
.panel--b{left:300px;top:487px;width:590px;height:280px}

.blob{position:absolute;border-radius:50%}
.blob--purple{background:var(--purple)}
.blob--teal{background:var(--teal)}
.blob--dark{background:#221c40}

.card{
  position:absolute;
  border-radius:30px;
  border:2px solid transparent;
  background:
    linear-gradient(var(--card),var(--card)) padding-box,
    linear-gradient(135deg,var(--teal) 0%,var(--purple) 55%,var(--teal) 100%) border-box;
  box-shadow:0 0 14px rgba(125,107,227,.35);
  overflow:hidden;
}
.panel--d1 .card{left:29px;top:28px;width:507px;height:283px}
.panel--a .card{left:83px;top:28px;width:405px;height:283px;overflow:visible}
.panel--b .card{left:88px;top:30px;width:424px;height:211px}

.abs{position:absolute;white-space:nowrap}
.code{font-family:"Ubuntu",sans-serif;font-size:10px;color:var(--teal-soft)}
.raf{font-family:"Ubuntu",sans-serif;font-size:10px;color:var(--teal-soft)}
.desc{font-size:5px;color:var(--text)}
.pill{
  position:absolute;height:11px;border-radius:6px;
  background:var(--purple);
  border:1.5px solid #b3a8ff;
  font-size:5px;color:#fff;text-align:center;line-height:8px;
}
.chev{position:absolute;width:8px;height:6px}

/* Dashboard 1 header */
.brand{left:26px;top:20px;display:flex;align-items:center;gap:6px}
.brand__mark{width:10px;height:10px;background:var(--purple)}
.brand__name{font-family:"Ubuntu",sans-serif;font-size:11px;color:var(--text);letter-spacing:.6px}
.app-title{left:153px;top:10px;font-family:"Ubuntu",sans-serif;font-size:22px;color:var(--purple-soft)}
.patient{left:387px;top:16px;font-size:9px}
.patient__meta{left:387px;top:33px;font-size:5px;color:var(--muted)}
.summary{left:134px;top:57px;font-size:8.5px}
.search{
  position:absolute;left:207px;top:55px;width:108px;height:15px;
  border:1.5px solid var(--teal);border-radius:8px;
  font-size:5px;color:var(--muted);padding:3px 0 0 16px;
}
.search svg{position:absolute;left:4px;top:2px}
.stat{font-size:6.5px;color:var(--teal-soft);top:59px}
.stat--white{color:#fff}
.count-badge{
  position:absolute;left:432px;top:56px;width:12px;height:12px;border-radius:50%;
  border:1px solid var(--purple-soft);font-size:7px;text-align:center;line-height:10px;color:#fff;
}
.col-head{font-size:6.5px;top:95px;display:flex;align-items:center;gap:4px}
.col-head i{display:inline-block;width:6px;height:6px;border-radius:50%;background:var(--purple)}
.col-rule{position:absolute;top:108px;height:3px;border-radius:2px;background:var(--purple)}

/* Expand rows */
.why{font-size:5.5px;color:#fff}
.why b{font-weight:700}
.band{position:absolute;left:0;right:0}
.band--light{background:var(--band)}
.band--dark{background:var(--band-dark)}
.row-label{font-size:7px}
.row-source{font-size:7px;font-weight:700}
.btn{
  position:absolute;display:flex;align-items:center;justify-content:center;gap:5px;
  border-radius:9px;font-family:"Ubuntu",sans-serif;color:#fff;white-space:nowrap;
}
.btn--purple{background:var(--purple);font-size:9px}
.btn--teal{background:var(--teal);font-size:7.5px}
.popup{
  position:absolute;border-radius:8px;
  border:2px solid var(--purple-soft);
  background:#1d1838;
  box-shadow:0 0 10px 2px rgba(31,201,185,.55);
}
.popup__key{font-size:6.5px;color:var(--teal-soft)}
.popup__title{font-size:6.5px;color:var(--purple-soft)}
.popup__text{font-size:5.5px;line-height:7px;color:#fff}
.lab-title{font-size:7px;font-weight:700}
.lab-text{font-size:6px;line-height:10px}
.history{font-size:7px;color:var(--teal-soft)}
.history-list{font-size:6px;line-height:10.3px}
.divider{position:absolute;height:2px;background:var(--teal)}
</style>
</head>
<body>

<svg width="0" height="0" style="position:absolute">
  <defs>
    <symbol id="chev-down" viewBox="0 0 8 6"><polyline points="1,1 4,4.5 7,1" fill="none" stroke="#fff" stroke-width="1.6"/></symbol>
    <symbol id="chev-up" viewBox="0 0 8 6"><polyline points="1,5 4,1.5 7,5" fill="none" stroke="#fff" stroke-width="1.6"/></symbol>
    <symbol id="doc-chart" viewBox="0 0 12 10"><rect x="0.5" y="0.5" width="11" height="9" fill="none" stroke="#fff" stroke-width="1"/><rect x="2.5" y="5" width="1.5" height="3" fill="#fff"/><rect x="5.2" y="3.5" width="1.5" height="4.5" fill="#fff"/><rect x="8" y="2" width="1.5" height="6" fill="#fff"/></symbol>
  </defs>
</svg>

<h1 class="board-title board-title--d1">Dashboard 1</h1>
<h1 class="board-title board-title--a">Dashboard Expand A</h1>
<h1 class="board-title board-title--b">Dashboard Expand B</h1>

<!-- Dashboard 1 -->
<section class="panel panel--d1">
  <div class="blob blob--dark" style="left:300px;top:-120px;width:420px;height:200px"></div>
  <div class="blob blob--purple" style="left:500px;top:75px;width:160px;height:200px"></div>
  <div class="blob blob--teal" style="left:-60px;top:118px;width:110px;height:150px"></div>
  <div class="blob blob--teal" style="left:300px;top:280px;width:360px;height:200px"></div>

  <div class="card">
    <div class="abs brand"><span class="brand__mark"></span><span class="brand__name">MEDVISTA</span></div>
    <div class="abs app-title">C-CDA Compendium</div>
    <div class="abs patient">Patient, Mary</div>
    <div class="abs patient__meta">Female | 01/11/1951 | Age: 70</div>
    <svg class="abs" style="left:474px;top:18px" width="10" height="11" viewBox="0 0 10 11"><path d="M5 1c2 0 3 1.5 3 3.5V7l1 1.5H1L2 7V4.5C2 2.5 3 1 5 1z" fill="var(--teal)"/><circle cx="5" cy="9.8" r="1" fill="var(--teal)"/><circle cx="8.5" cy="1.8" r="1.5" fill="var(--teal-soft)"/></svg>

    <svg class="chev" style="left:120px;top:60px"><use href="#chev-down" stroke="var(--teal)"/></svg>
    <div class="abs summary">HCC Summary</div>
    <div class="search"><svg width="9" height="9" viewBox="0 0 9 9"><circle cx="3.7" cy="3.7" r="2.7" fill="none" stroke="#fff" stroke-width="1"/><line x1="5.8" y1="5.8" x2="8.3" y2="8.3" stroke="#fff" stroke-width="1"/></svg>Search...</div>
    <div class="abs stat" style="left:334px">RAF: 2.362</div>
    <div class="abs stat stat--white" style="left:374px">Condition Count</div>
    <div class="count-badge">8</div>
    <div class="abs stat" style="left:448px">ID: 7326472</div>

    <div class="abs col-head" style="left:134px">ICD-10 Code <i></i></div>
    <div class="abs col-head" style="left:239px">Condition <i></i></div>
    <div class="abs col-head" style="left:355px">Catagory <i></i></div>
    <div class="abs col-head" style="left:437px">RAF <i></i></div>
    <div class="col-rule" style="left:134px;width:52px"></div>
    <div class="col-rule" style="left:232px;width:54px"></div>
    <div class="col-rule" style="left:349px;width:53px"></div>

    <div class="abs code" style="left:134px;top:121px">J44.9</div>
    <div class="abs desc" style="left:210px;top:124px">Chronic obstructive pulmonary disease</div>
    <div class="pill" style="left:349px;top:122px;width:52px">111</div>
    <div class="abs raf" style="left:434px;top:121px">0.335</div>
    <svg class="chev" style="left:467px;top:125px"><use href="#chev-down"/></svg>

    <div class="abs code" style="left:134px;top:148px">F33.1</div>
    <div class="abs desc" style="left:210px;top:151px">Chronic kidney disease, moderate (stage 3)</div>
    <div class="pill" style="left:349px;top:149px;width:52px">138</div>
    <div class="abs raf" style="left:434px;top:148px">0.069</div>
    <svg class="chev" style="left:467px;top:152px"><use href="#chev-down"/></svg>

    <div class="abs code" style="left:134px;top:175px">F33.0</div>
    <div class="abs desc" style="left:210px;top:178px">Major depressive disorder, recurrent, mild</div>
    <div class="pill" style="left:349px;top:176px;width:52px">59</div>
    <div class="abs raf" style="left:434px;top:175px">0.309</div>
    <svg class="chev" style="left:467px;top:179px"><use href="#chev-down"/></svg>

    <div class="abs code" style="left:134px;top:202px">I42.9</div>
    <div class="abs desc" style="left:210px;top:205px">cardiomyopathy</div>
    <div class="pill" style="left:349px;top:203px;width:52px">85</div>
    <div class="abs raf" style="left:434px;top:202px">0.447</div>
    <svg class="chev" style="left:467px;top:206px"><use href="#chev-down"/></svg>

    <div class="abs code" style="left:134px;top:229px">E11.36</div>
    <div class="abs desc" style="left:210px;top:232px">Type 2 diabetes mellitus with diabetic cataract</div>
    <div class="pill" style="left:349px;top:230px;width:52px">18</div>
    <div class="abs raf" style="left:434px;top:229px">0.302</div>
    <svg class="chev" style="left:467px;top:233px"><use href="#chev-down"/></svg>
  </div>
</section>

<!-- Dashboard Expand A -->
<section class="panel panel--a">
  <div class="blob blob--dark" style="left:280px;top:-120px;width:420px;height:200px"></div>
  <div class="blob blob--purple" style="left:480px;top:70px;width:180px;height:230px"></div>
  <div class="blob blob--teal" style="left:515px;top:160px;width:120px;height:120px"></div>
  <div class="blob blob--teal" style="left:-40px;top:120px;width:120px;height:160px"></div>
  <div class="blob blob--teal" style="left:300px;top:285px;width:360px;height:200px"></div>

  <div class="card">
    <div style="position:absolute;inset:0;border-radius:28px;overflow:hidden">
      <div class="band band--light" style="top:74px;height:41px"></div>
      <div class="band band--dark" style="top:115px;height:55px"></div>
      <div class="band band--light" style="top:170px;height:41px"></div>
      <div class="band band--dark" style="top:211px;height:72px"></div>
    </div>
    <div class="abs code" style="left:32px;top:26px">E11.36</div>
    <div class="abs desc" style="left:107px;top:29px">Type 2 diabetes mellitus with diabetic cataract</div>
    <div class="pill" style="left:246px;top:26px;width:52px">18</div>
    <div class="abs raf" style="left:332px;top:26px">0.302</div>
    <svg class="chev" style="left:364px;top:29px"><use href="#chev-up"/></svg>
    <div class="abs why" style="left:70px;top:50px"><b>Why:</b> This Patient was treated for cataracts that may be associated with type 2 diabetes melitus</div>

    <div class="abs row-label" style="left:35px;top:90px">Extacpsular cataract With IOL</div>
    <div class="abs row-source" style="left:170px;top:90px">C-CDA: Procedures</div>
    <div class="btn btn--purple" style="left:277px;top:84px;width:91px;height:18px"><svg width="12" height="10"><use href="#doc-chart"/></svg>View Source</div>

    <div class="abs row-label" style="left:35px;top:185px">Diabetes Type 2</div>
    <div class="abs row-source" style="left:170px;top:185px">C-CDA: Problem list</div>
    <div class="btn btn--purple" style="left:277px;top:180px;width:91px;height:18px"><svg width="12" height="10"><use href="#doc-chart"/></svg>View Source</div>
  </div>

  <div class="popup" style="left:19px;top:141px;width:326px;height:57px">
    <div class="abs popup__key" style="left:27px;top:23px">Cataract</div>
    <div class="abs popup__title" style="left:98px;top:14px">Ophthalmology Chart Note</div>
    <div class="abs popup__text" style="left:98px;top:24px">Patient presents for cataract<br>evaluation in the right eye.</div>
    <div class="btn btn--teal" style="left:221px;top:17px;width:77px;height:18px"><svg width="10" height="8"><use href="#doc-chart"/></svg>View Source</div>
  </div>

  <div class="popup" style="left:214px;top:237px;width:326px;height:57px">
    <div class="abs popup__key" style="left:26px;top:25px">HbA1c</div>
    <div class="abs popup__title" style="left:97px;top:11px">Lab Results</div>
    <div class="abs popup__text" style="left:97px;top:20px">Hemoglobin A1C<br>6.9%<br>01/15/21</div>
    <div class="btn btn--teal" style="left:222px;top:18px;width:76px;height:17px"><svg width="10" height="8"><use href="#doc-chart"/></svg>View Source</div>
  </div>
</section>

<!-- Dashboard Expand B -->
<section class="panel panel--b">
  <div class="blob blob--dark" style="left:100px;top:-150px;width:380px;height:190px"></div>
  <div class="blob blob--purple" style="left:470px;top:55px;width:220px;height:220px"></div>
  <div class="blob blob--teal" style="left:540px;top:150px;width:120px;height:140px"></div>
  <div class="blob blob--teal" style="left:-30px;top:150px;width:160px;height:200px"></div>

  <div class="card">
    <div class="band band--light" style="top:78px;height:52px"></div>
    <div class="band band--dark" style="top:130px;height:81px"></div>
    <div class="abs code" style="left:34px;top:27px">N18.31</div>
    <div class="abs desc" style="left:112px;top:30px">Chronic kidney disease, stage 3a</div>
    <div class="pill" style="left:258px;top:27px;width:55px">138</div>
    <div class="abs raf" style="left:348px;top:27px">0.069</div>
    <svg class="chev" style="left:381px;top:30px"><use href="#chev-up"/></svg>
    <div class="abs why" style="left:132px;top:53px"><b>Why:</b> This patient has an eGFR between 45-59 mL/min</div>

    <div class="abs row-label" style="left:37px;top:98px;font-weight:700">eGFR</div>
    <div class="abs lab-title" style="left:178px;top:86px">Lab Results</div>
    <div class="abs lab-text" style="left:178px;top:96px">47mL/min<br>05/26/2021</div>
    <div class="btn btn--purple" style="left:291px;top:89px;width:95px;height:19px"><svg width="12" height="10"><use href="#doc-chart"/></svg>View Source</div>

    <div class="divider" style="left:139px;top:129px;width:146px"></div>
    <div class="abs history" style="left:203px;top:142px">History</div>
    <div class="abs history-list" style="left:182px;top:154px">45 mL/min<br>41 mL/min<br>52 mL/min<br>44 mL/min</div>
    <div class="abs history-list" style="left:222px;top:154px">03/17/21<br>01/14/21<br>10/15/20<br>06/22/20</div>
  </div>
</section>

</body>
</html>
```